Create a memorable Stationary for Security Software Company

Velbrantix is the worldwide leader in securing the Internet. Making Internet communications and critical data secure, reliable and available everywhere has been and continues to be our ongoing vision. We are committed to staying focused on real customer needs and to developing new and innovative security solutions that redefine the security landscape.

Industry/Entity Type

Internet

Font styles to use
Serif
Sans Serif
Script

Colors
0792cd
33a6d7
85cae6

```html
<!DOCTYPE html>
<html lang="en">
<head>
<meta charset="utf-8">
<title>Velbrantix Business Card</title>
<link rel="stylesheet" href="https://fonts.googleapis.com/css2?family=Open+Sans:wght@400;600;700&display=swap">
<style>
  :root {
    --brand-deep: #0792cd;
    --brand-mid: #33a6d7;
    --brand-light: #85cae6;
    --card-top: #b3e0f3;
    --card-bottom: #7cc3e2;
    --panel-top: #5bb8e2;
    --panel-bottom: #2f9fd3;
    --ink-contact: #145f86;
    --ink-name: #0d6f9f;
    --ink-title: #2f5f78;
    --page-bg: #e8eef2;
  }
  * { margin: 0; padding: 0; box-sizing: border-box; }
  html, body {
    width: 1200px;
    height: 843px;
    overflow: hidden;
    background: var(--page-bg);
    font-family: "Open Sans", Arial, sans-serif;
  }
  .card {
    position: absolute;
    left: 290px;
    width: 620px;
    height: 354px;
    border-radius: 26px;
    overflow: hidden;
    background: linear-gradient(160deg, var(--card-top) 0%, var(--brand-light) 45%, var(--card-bottom) 100%);
  }
  .card-back { top: 44px; }
  .card-front { top: 444px; }

  /* Back side */
  .back-lockup {
    position: absolute;
    left: 0;
    right: 0;
    top: 140px;
    display: flex;
    justify-content: center;
    align-items: center;
    gap: 12px;
  }
  .back-url {
    position: absolute;
    left: 0;
    right: 0;
    bottom: 34px;
    text-align: center;
    font-size: 15px;
    letter-spacing: 6px;
    color: var(--brand-deep);
  }

  /* Front side */
  .illustration-panel {
    position: absolute;
    left: 0;
    top: 0;
    width: 286px;
    height: 354px;
    background: linear-gradient(175deg, var(--panel-top) 0%, var(--panel-bottom) 100%);
    opacity: 0.85;
  }
  .contact-list {
    position: absolute;
    left: 34px;
    top: 112px;
    list-style: none;
    color: var(--ink-contact);
    font-size: 15px;
    line-height: 24px;
  }
  .contact-list li {
    display: flex;
    align-items: center;
    gap: 9px;
    white-space: nowrap;
  }
  .contact-icon {
    width: 14px;
    height: 14px;
    flex: none;
    fill: var(--ink-contact);
  }
  .front-lockup {
    position: absolute;
    right: 38px;
    top: 110px;
    display: flex;
    align-items: center;
    gap: 10px;
  }
  .brand-dot {
    width: 28px;
    height: 28px;
    border-radius: 50%;
    background: var(--brand-mid);
  }
  .brand-name {
    font-size: 28px;
    font-weight: 600;
    color: var(--brand-deep);
    letter-spacing: 0.3px;
  }
  .holder {
    position: absolute;
    right: 38px;
    bottom: 38px;
    text-align: right;
  }
  .holder-name {
    font-size: 21px;
    font-weight: 700;
    color: var(--ink-name);
    line-height: 26px;
  }
  .holder-title {
    font-size: 15px;
    color: var(--ink-title);
    line-height: 20px;
  }
</style>
</head>
<body>
  <article class="card card-back">
    <div class="back-lockup">
      <span class="brand-dot" aria-hidden="true"></span>
      <span class="brand-name">Velbrantix</span>
    </div>
    <p class="back-url">www.velbrantix.com</p>
  </article>

  <article class="card card-front">
    <div class="illustration-panel" role="img" aria-label="Decorative cloud illustration panel"></div>

    <ul class="contact-list">
      <li>4120 Harbor View Road</li>
      <li>Fairbanks, Alaska 99701</li>
      <li>
        <svg class="contact-icon" viewBox="0 0 24 24" aria-label="Phone"><path d="M6.6 10.8a15.1 15.1 0 0 0 6.6 6.6l2.2-2.2c.3-.3.7-.4 1-.2 1.1.4 2.3.6 3.6.6.6 0 1 .4 1 1V20c0 .6-.4 1-1 1A17 17 0 0 1 3 4c0-.6.4-1 1-1h3.5c.6 0 1 .4 1 1 0 1.3.2 2.5.6 3.6.1.3 0 .7-.2 1z"/></svg>
        689 555 0148
      </li>
      <li>
        <svg class="contact-icon" viewBox="0 0 24 24" aria-label="Fax"><path d="M7 3h10v5H7zM4 9h16a2 2 0 0 1 2 2v6h-4v4H6v-4H2v-6a2 2 0 0 1 2-2zm4 7v3h8v-3z"/></svg>
        482 555 0193
      </li>
      <li>
        <svg class="contact-icon" viewBox="0 0 24 24" aria-label="Email"><path d="M2 5h20v14H2zm2 2v.5l8 5 8-5V7zm0 2.8V17h16V9.8l-8 5z"/></svg>
        hello@velbrantix.com
      </li>
      <li>
        <svg class="contact-icon" viewBox="0 0 24 24" aria-label="Website"><circle cx="12" cy="12" r="9" fill="none" stroke="currentColor" stroke-width="2" style="stroke:var(--ink-contact)"/><path d="M3 12h18M12 3c3 3 3 15 0 18M12 3c-3 3-3 15 0 18" fill="none" stroke-width="1.6" style="stroke:var(--ink-contact)"/></svg>
        www.velbrantix.com
      </li>
    </ul>

    <div class="front-lockup">
      <span class="brand-dot" aria-hidden="true"></span>
      <span class="brand-name">Velbrantix</span>
    </div>

    <div class="holder">
      <p class="holder-name">Daniel Ortmann</p>
      <p class="holder-title">CEO/Founder</p>
    </div>
  </article>
</body>
</html>
```